Captivating packaging design for sports company.

We need a packaging design that encompasses our resistance bands workout set. Our focus is quality, convenience, and versatility. The design should be tailored to our broad array of customer across all paths. We would like the packaging to reflect our brand and product features such as: the LBS(weight) listed on each of the bands, convenience for travel and at home, highest quality, for all fitness levels, and free eBook. We'd also like to include a couple of our reviews on the packaging. Please refer to our listing on Varlo for additional information https://www.shopvarlo.com/Brisklane-Athletics-Resistance-Workout-Carrying/dp/K47TR2XMNQ/ref=sr_1_1?ie=UTF8&qid=1470453588&sr=8-1&keywords=brisklane+athletics+resistance+bands
Please reach out with additional questions for any further details. Thank you.
Target Market(s)
Sports, fitness, and health enthusiasts of all ages.
Industry/Entity Type
It Company
Look and feel
Each slider illustrates characteristics of the customer's brand and the style your logo design should communicate.

```html
<!DOCTYPE html>
<html lang="en">
<head>
<meta charset="utf-8">
<title>Brisklane Athletics – Resistance Bands Packaging</title>
<link rel="stylesheet" href="https://fonts.googleapis.com/css2?family=Montserrat:wght@500;700;800;900&family=Michroma&display=swap">
<style>
  :root {
    --navy: #1b2d57;
    --navy-deep: #15244a;
    --sky: #9fd4f2;
    --sky-soft: #b6def5;
    --accent: #2a80c4;
    --ink-blue: #2470b0;
    --white: #ffffff;
    --stage: #e4e4e4;
  }
  * { box-sizing: border-box; margin: 0; padding: 0; }
  html, body { width: 1200px; height: 1199px; overflow: hidden; }
  body {
    background: var(--stage);
    font-family: "Montserrat", Arial, sans-serif;
    position: relative;
  }
  .dieline { position: absolute; left: 150px; top: 150px; width: 900px; height: 900px; }

  /* top flap */
  .panel-top {
    position: absolute; left: 260px; top: 0; width: 640px; height: 190px;
    background: var(--sky-soft);
    display: flex; align-items: center; justify-content: center;
  }
  .panel-top .brand { transform: rotate(180deg); }

  /* side panel */
  .panel-side {
    position: absolute; left: 0; top: 190px; width: 260px; height: 710px;
    background: var(--navy); color: var(--white);
  }
  .panel-side .brand { position: absolute; left: 26px; top: 44px; }
  .contents {
    position: absolute; left: 26px; right: 26px; top: 170px;
    font-size: 12px; font-weight: 700; line-height: 1.45; text-align: center; letter-spacing: .5px;
  }
  .slogan {
    position: absolute; left: 26px; top: 360px;
    font-size: 50px; font-weight: 800; line-height: 1.05; letter-spacing: 3px;
  }
  .resistance-note {
    position: absolute; left: 16px; right: 0; bottom: 0; height: 150px;
    background: var(--sky); color: var(--navy);
    padding: 30px 18px; font-size: 19px; font-weight: 800; line-height: 1.15; text-align: center;
  }

  /* front panel */
  .panel-front {
    position: absolute; left: 260px; top: 190px; width: 640px; height: 710px;
    background: var(--sky); overflow: hidden;
  }
  .panel-front > * { position: absolute; z-index: 1; }
  .panel-front > .hero-photo { z-index: 0; left: 0; top: 0; width: 280px; height: 710px; }

  .panel-front .brand-main {
    left: 330px; top: 70px; width: 260px;
    display: flex; flex-direction: column; align-items: center; gap: 12px;
  }
  .brand { display: flex; align-items: center; gap: 10px; }
  .brand-mark { width: 30px; height: 30px; border-radius: 50%; background: currentColor; flex: none; }
  .brand-name { font-weight: 800; font-size: 17px; line-height: 1.05; letter-spacing: .5px; text-transform: uppercase; }
  .panel-side .brand { color: var(--white); }
  .panel-top .brand { color: var(--navy); }
  .brand-main .brand-mark { width: 54px; height: 54px; background: var(--navy-deep); }
  .brand-main .brand-name { font-size: 26px; color: var(--navy-deep); text-align: center; }

  .title-band {
    left: 250px; right: 0; top: 245px; height: 150px;
    background: var(--navy); color: var(--white);
    padding: 22px 0 0 30px;
    border-bottom: 8px solid var(--accent);
  }
  .title-band .kicker { font-size: 21px; font-weight: 700; letter-spacing: 1px; }
  .title-band h1 { font-size: 44px; font-weight: 800; line-height: 1.02; letter-spacing: 1px; }

  .set-name {
    left: 300px; top: 420px;
    font-family: "Michroma", "Montserrat", sans-serif; color: var(--ink-blue);
    font-size: 20px; line-height: 1.3; white-space: nowrap;
  }
  .set-list {
    left: 300px; top: 525px; list-style: none;
    font-family: "Michroma", "Montserrat", sans-serif; color: var(--ink-blue);
    font-size: 13px; line-height: 1.45; white-space: nowrap;
  }
  .badge {
    left: 515px; top: 560px; width: 90px; height: 90px;
    border-radius: 50%; border: 3px solid var(--accent);
  }
  .bonus {
    left: 90px; top: 520px; width: 170px; height: 170px;
    border-radius: 50%; background: var(--navy); color: var(--white);
    padding: 30px 14px; text-align: center;
  }
  .bonus strong { display: block; font-size: 30px; font-weight: 800; letter-spacing: 1px; }
  .bonus span { display: block; font-size: 15px; font-weight: 700; line-height: 1.15; }
</style>
</head>
<body>
  <main class="dieline">
    <section class="panel-top">
      <div class="brand"><span class="brand-mark"></span><span class="brand-name">Brisklane<br>Athletics</span></div>
    </section>

    <section class="panel-side">
      <div class="brand"><span class="brand-mark"></span><span class="brand-name">Brisklane<br>Athletics</span></div>
      <p class="contents">
        IN THE BOX<br>
        x1 YELLOW - 2-4LB<br>
        x1 GREEN - 4-6LB<br>
        x1 BLUE - 10-12LB<br>
        x1 RED - 15-20LB<br>
        x1 BLACK - 25-30LB<br>
        CARRY CASE<br>
        E-BOOK
      </p>
      <p class="slogan">TONE<br>BURN<br>BUILD</p>
      <p class="resistance-note">UP TO 75LBS<br>OF TOTAL<br>RESISTANCE</p>
    </section>

    <section class="panel-front">
      <svg class="hero-photo" role="img" aria-label="Photo of an athlete in a blue shirt training with a resistance band" viewBox="0 0 280 710" preserveAspectRatio="none">
        <defs>
          <linearGradient id="heroTone" x1="0" y1="0" x2="1" y2="1">
            <stop offset="0" stop-color="#9fd4f2"/>
            <stop offset=".45" stop-color="#3a6fae"/>
            <stop offset="1" stop-color="#1c2c4c"/>
          </linearGradient>
        </defs>
        <rect width="280" height="710" fill="url(#heroTone)"/>
      </svg>

      <div class="brand-main">
        <span class="brand-mark"></span>
        <span class="brand-name">Brisklane<br>Athletics</span>
      </div>

      <div class="title-band">
        <p class="kicker">HIGH QUALITY</p>
        <h1>RESISTANCE<br>BANDS</h1>
      </div>

      <p class="set-name">Brisklane Athletics<br>Resistance Band<br>Workout Set</p>
      <ul class="set-list">
        <li>4 Colourful Bands</li>
        <li>Door Anchor</li>
        <li>2 Handles</li>
        <li>2 Ankle Straps</li>
        <li>Carrying Case</li>
      </ul>
      <div class="badge" role="img" aria-label="Indoors or outdoors badge"></div>

      <div class="bonus">
        <strong>BONUS</strong>
        <span>Product and<br>Workout<br>Guide eBook</span>
      </div>
    </section>
  </main>
</body>
</html>
```